KRL Stationery Design Project

Dear Designers,
We need a new stationery design for company to match our new logo.
Designers should provide a design for the following:
1. Business Card: 3.5x2 Inches.
2. Letterhead: A4 size.
3. Envelops: 25x35.5 Cm.
You can keep the Arabic name at the bottom of the logo Or you can use the separate attached Arabic Name.
Please refer to the attached logo guide for design information.
Sample Business Card information:
Name: Tarek Sowan
Position: Operation Manager
Tel: +966 920007164 Ex. 500
Fax: +966 (3)8842617
Mob: +966 (5)00263817
email: tarek@krl-example.com.sa
URL: www.krl-example.com.sa
Address:
Nakheel Heights, Suite 718
Zayed bin Omar Str.
Khobar, 31847
Saudi Arabia
Updates
Dear All,
Please note, we had uploaded our logo along with Arabic writing in Adobe illustrator format (.ai).
Regards,
Karim
Dear All,
A sample data for the business card had been added as per your request.
Regards,
Karim

```html
<!DOCTYPE html>
<html lang="en">
<head>
<meta charset="utf-8">
<title>KRL Business Card</title>
<link href="https://fonts.googleapis.com/css2?family=Source+Sans+3:ital,wght@0,400;0,700;1,700&display=swap" rel="stylesheet">
<style>
  :root {
    --backdrop: #2b2b2d;
    --card: #ffffff;
    --navy: #132d52;
    --grey: #a3a4a6;
    --ink: #333333;
    --white: #ffffff;
  }
  * { margin: 0; padding: 0; box-sizing: border-box; }
  html, body { width: 960px; height: 1200px; overflow: hidden; }
  body {
    background: var(--backdrop);
    font-family: "Source Sans 3", Arial, sans-serif;
    color: var(--ink);
    position: relative;
  }
  .card {
    position: absolute;
    background: var(--card);
    border-radius: 28px;
    overflow: hidden;
  }
  .card--front { left: 62px; top: 86px; width: 838px; height: 481px; }
  .card--back  { left: 58px; top: 624px; width: 839px; height: 480px; }

  .brand {
    position: absolute;
    display: flex;
    align-items: center;
    gap: 18px;
    color: var(--navy);
    font-weight: 700;
    line-height: 1;
  }
  .brand__mark { background: var(--navy); display: block; }
  .card--front .brand { left: 48px; top: 70px; font-size: 110px; }
  .card--front .brand__mark { width: 44px; height: 44px; }
  .card--back .brand { left: 50%; top: 50%; transform: translate(-50%, -50%); font-size: 170px; }
  .card--back .brand__mark { width: 64px; height: 64px; }

  .contact {
    position: absolute;
    left: 56px;
    top: 296px;
    font-size: 20px;
    line-height: 32px;
    list-style: none;
  }
  .contact b { font-style: italic; font-weight: 700; }
  .contact .sep { margin: 0 6px; }

  .address {
    position: absolute;
    right: 74px;
    top: 331px;
    font-size: 20px;
    line-height: 28px;
    text-align: right;
    font-style: normal;
  }

  .swoosh { position: absolute; left: 0; bottom: 0; width: 838px; height: 90px; }

  .person {
    position: absolute;
    left: 401px;
    top: 432px;
    color: var(--white);
    font-size: 25px;
  }
  .person__role { font-size: 20px; }
</style>
</head>
<body>
  <section class="card card--front">
    <div class="brand"><span class="brand__mark"></span><span class="brand__name">KRL</span></div>

    <ul class="contact">
      <li><b>t</b> : 123-123-1234<span class="sep">|</span><b>f</b> : 123-123-1234</li>
      <li><b>e</b> : info@krl-example.com.sa</li>
      <li><b>w</b> : www.krl-example.com.sa</li>
    </ul>

    <address class="address">
      1234, Suite# 123, Street Name<br>
      State Name, Country Code
    </address>

    <svg class="swoosh" viewBox="0 0 838 90" aria-hidden="true">
      <path d="M0 44 C150 24 320 12 430 0 C340 10 180 30 20 80 L0 82 Z" fill="var(--grey)"/>
      <path d="M30 90 C200 40 420 2 480 0 C640 -4 760 8 838 20 L838 90 Z" fill="var(--navy)"/>
    </svg>

    <p class="person">Your Name, <span class="person__role">Designation</span></p>
  </section>

  <section class="card card--back">
    <div class="brand"><span class="brand__mark"></span><span class="brand__name">KRL</span></div>
  </section>
</body>
</html>
```